Larkhollow needs a Webpage Design

We need a webpage for Dr. XYZ who is doing consultancy practice in the area of speech, language, and reading disabilities. He is doing his consultancy practice as "Larkhollow Consultants". Our target market is clients with annual income of $100,000 or more in Chicago area. Our business philosophy is: "...We provide the best evidence-based services/interventions, at an affordable fee, and deal only with clients who seek such services...."

Dr. XYZ's area of research interests are: a) using assistive technology for communication for children with autism, b) early intervention with focus on parent participation, and c) language learning for children birth-to-five years.

He works at a public university whose school color is 'Orange". Home page should show two logos (university and practice). Each page should stand on its own and reflect the content with minimal scrolling. The colors should be subdued (not bright colors) to attract college educated wealthy individuals who are seeking best evidence-based practice in speech, language, and reading for their children.

We need five pages: Home, Consultation, Research, Professional Development, and Contact (with google map directions). The home page should have space for a picture and links for facebook, twitter, and google plus. Other pages should have space for at least one picture and links to pdf files.

The overall design should show healthcare service, evidence-based early intervention with focus on parent participation, and project that we are leaders in the field.

```html
<!DOCTYPE html>
<html lang="en">
<head>
<meta charset="utf-8">
<title>Larkhollow Consultants</title>
<link rel="stylesheet" href="https://fonts.googleapis.com/css2?family=Quicksand:wght@500;600&family=Arimo:wght@400&display=swap">
<style>
:root{
  --brand:#456b93;
  --brand-dark:#3f6790;
  --text:#555a60;
  --muted:#666;
  --line:#dcdcdc;
  --panel:#f6f6f6;
  --white:#fff;
}
*{margin:0;padding:0;box-sizing:border-box}
html,body{width:994px;height:1200px;overflow:hidden;background:var(--white)}
body{position:relative;font-family:"Arimo",Arial,sans-serif;color:var(--text)}
.site-header{position:absolute;left:0;top:0;width:994px;height:61px;border-bottom:1px solid #e6e6e6}
.brand{position:absolute;left:144px;top:13px;display:flex;align-items:center;gap:8px;font-family:"Quicksand",sans-serif;font-weight:600;color:var(--brand-dark)}
.brand-dot{width:30px;height:30px;border-radius:50%;background:var(--brand)}
.brand-name{font-size:20px;line-height:20px}
.brand-name small{display:block;font-size:11px;letter-spacing:3.2px;line-height:13px}
.main-nav a{position:absolute;top:27px;font-size:9px;color:#666;text-decoration:none;white-space:nowrap}
.hero{position:absolute;left:0;top:61px;width:994px;height:388px;background:linear-gradient(110deg,#b47a6c 0%,#d9b39b 30%,#c9a083 50%,#8e9a80 70%,#c26b5c 100%)}
.hero-arrow{position:absolute;top:174px;width:38px;height:38px}
.hero-caption{position:absolute;left:142px;background:rgba(69,107,147,.9);color:var(--white);font-family:"Quicksand",sans-serif;font-weight:600;font-size:14.5px;height:37px;line-height:37px;padding:0 20px;white-space:nowrap}
.feature{position:absolute;top:486px;width:200px;text-align:center}
.feature svg{display:block;margin:0 auto;height:62px}
.feature h2{font-family:"Quicksand",sans-serif;font-weight:600;font-size:14px;color:var(--brand);margin-top:14px;white-space:nowrap}
.feature p{width:182px;margin:8px auto 0;font-size:8.6px;line-height:17px;color:var(--muted)}
.btn{display:inline-block;background:var(--brand);color:var(--white);font-family:"Quicksand",sans-serif;font-weight:600;font-size:9px;text-decoration:none;text-align:center;border-radius:2px}
.feature .btn{width:84px;height:22px;line-height:22px;margin-top:15px}
.join{position:absolute;left:142px;top:725px;width:711px;height:61px;background:var(--panel);border:1px solid var(--line)}
.join p{position:absolute;left:20px;top:12px;width:540px;font-size:9.3px;line-height:18px;color:var(--muted)}
.join .btn{position:absolute;left:571px;top:16px;width:126px;height:30px;line-height:30px;font-size:9.5px}
.research-title{position:absolute;top:818px;width:994px;text-align:center;font-family:"Quicksand",sans-serif;font-weight:600;font-size:14px;color:var(--brand)}
.research-intro{position:absolute;left:170px;top:848px;width:654px;text-align:center;font-size:10px;line-height:21px;color:var(--muted)}
.topic{position:absolute;top:914px;width:219px;text-align:center}
.topic-photo{width:219px;height:120px}
.topic p{width:186px;margin:12px auto 0;font-size:9.5px;line-height:17px;color:var(--brand)}
.site-footer{position:absolute;left:0;top:1124px;width:994px;height:76px;background:var(--brand-dark);color:var(--white)}
.footer-nav a{position:absolute;top:22px;font-size:9px;color:var(--white);text-decoration:none}
.copyright{position:absolute;left:142px;top:44px;font-size:8.5px}
.social{position:absolute;left:720px;top:26px;display:flex;align-items:center;gap:7px;font-size:8.5px}
.social span{margin-right:1px}
.social a{display:block;width:23px;height:23px;border-radius:50%;background:var(--white)}
</style>
</head>
<body>
<header class="site-header">
  <div class="brand"><span class="brand-dot"></span><span class="brand-name">Larkhollow<small>Consultants</small></span></div>
  <nav class="main-nav">
    <a href="#" style="left:398px">HOME</a>
    <a href="#" style="left:457px">CONSULTATION</a>
    <a href="#" style="left:557px">RESEARCH</a>
    <a href="#" style="left:638px">PROFESSIONAL DEVELOPMENT</a>
    <a href="#" style="left:804px">CONTACT</a>
  </nav>
</header>

<section class="hero" role="img" aria-label="Teacher smiling with a group of young children in a classroom">
  <svg class="hero-arrow" style="left:58px" viewBox="0 0 38 38"><circle cx="19" cy="19" r="18" fill="none" stroke="rgba(255,255,255,.5)" stroke-width="1.5"/><path d="M24 11 L12 19 L24 27 L21 19Z" fill="rgba(255,255,255,.55)"/></svg>
  <svg class="hero-arrow" style="left:895px" viewBox="0 0 38 38"><circle cx="19" cy="19" r="18" fill="none" stroke="rgba(255,255,255,.4)" stroke-width="1.5"/><path d="M14 11 L26 19 L14 27 L17 19Z" fill="rgba(255,255,255,.4)"/></svg>
  <div class="hero-caption" style="top:271px">We are doing consultancy practice</div>
  <div class="hero-caption" style="top:313px">in the area of speech, language, and reading disabilities</div>
</section>

<div class="feature" style="left:162px">
  <svg viewBox="0 0 60 62" fill="none" stroke="#456b93" stroke-width="2" stroke-linecap="round">
    <path d="M30 2v6M10 10l4 4M50 10l-4 4M4 30h6M56 30h-6M10 48l4-4M50 48l-4-4"/>
    <path d="M21 40c-3-3-6-7-6-12a15 15 0 0 1 30 0c0 5-3 9-6 12v5H21z"/>
    <path d="M26 38l-2-10 6 4 6-4-2 10M22 49h16M22 53h16M25 57h10"/>
  </svg>
  <h2>Consultation</h2>
  <p>It is a long established fact that a reader will be distracted by the readable content of a page when looking at its layout.</p>
  <a class="btn" href="#">READ MORE</a>
</div>
<div class="feature" style="left:401px">
  <svg viewBox="0 0 60 62" fill="none" stroke="#456b93" stroke-width="2" stroke-linecap="round">
    <circle cx="35" cy="24" r="16"/><path d="M23 36L8 53a3 3 0 0 0 4 4l15-17"/>
  </svg>
  <h2>Research</h2>
  <p>It is a long established fact that a reader will be distracted by the readable content of a page when looking at its layout.</p>
  <a class="btn" href="#">READ MORE</a>
</div>
<div class="feature" style="left:635px">
  <svg viewBox="0 0 60 62" fill="none" stroke="#456b93" stroke-width="2" stroke-linecap="round">
    <path d="M22 58V46c-6-4-10-10-10-18a20 20 0 0 1 40 0c0 8-3 14-6 18v10"/>
    <path d="M12 30l-4 8h5v6h9"/>
    <circle cx="26" cy="30" r="5"/><circle cx="39" cy="22" r="6"/><circle cx="39" cy="22" r="2"/>
  </svg>
  <h2>Professional Development</h2>
  <p>It is a long established fact that a reader will be distracted by the readable content of a page when looking at its layout.</p>
  <a class="btn" href="#">READ MORE</a>
</div>

<section class="join">
  <p>Content here, content here', making it look like readable English. Many desktop publishing packages and web page editors now use Lorem Ipsum as their default model text...</p>
  <a class="btn" href="#">JOIN NOW</a>
</section>

<h2 class="research-title">WE RESEARCH ON</h2>
<p class="research-intro">It is a long established fact that a reader will be distracted by the readable content of a page when looking at its layout. The point of using Lorem Ipsum is that it has a more-or-less normal distribution of letters, as opposed to using 'Content here content here...</p>

<div class="topic" style="left:142px">
  <div class="topic-photo" role="img" aria-label="Child's hands pressed against an orange surface" style="background:linear-gradient(135deg,#c8441e,#e0703e 50%,#b8381a)"></div>
  <p>Using assistive technology for communication for children with autism,</p>
</div>
<div class="topic" style="left:389px">
  <div class="topic-photo" role="img" aria-label="Parent and helper with a toddler in a bright room" style="background:linear-gradient(135deg,#c9ccd0,#e6e4e0 50%,#9fb0c6)"></div>
  <p style="width:170px">Early intervention with focus on parent participation</p>
</div>
<div class="topic" style="left:634px">
  <div class="topic-photo" role="img" aria-label="Group of smiling young children" style="background:linear-gradient(120deg,#c99a7a,#e2d2c6 50%,#9fb8cf)"></div>
  <p style="width:176px">language learning for children birth-to-five years.</p>
</div>

<footer class="site-footer">
  <nav class="footer-nav">
    <a href="#" style="left:142px">Home</a>
    <a href="#" style="left:191px">Consultation</a>
    <a href="#" style="left:265px">Research</a>
    <a href="#" style="left:327px">Professional Development</a>
    <a href="#" style="left:453px">Contact</a>
  </nav>
  <p class="copyright">Copyright © 2014. Larkhollow Consultants All Rights Reserved</p>
  <div class="social"><span>Follow us :</span><a href="#" aria-label="Social link one"></a><a href="#" aria-label="Social link two"></a><a href="#" aria-label="Social link three"></a></div>
</footer>
</body>
</html>
```